Fashion Label Startup Business Card Design

Miriam Kettle is a startup fashion designer based on the Gold Coast in QLD Australia. Miriams label " Verona by Kettle " is based upon taking old world design techniques and infusing them modern twist. The card design should incorporate an old world theme using colours like mustard, ocha, black, white and elements of lace pattern.

Card Details:

Miriam Kettle
Fashion Designer
P: 04 0261 5847
E: veronabykettle@mailbrook.example
W: www.socialpage.example/VEronaByKettle

```html
<!DOCTYPE html>
<html lang="en">
<head>
<meta charset="utf-8">
<title>Verona by Kettle – Business Card</title>
<link rel="stylesheet" href="https://fonts.googleapis.com/css2?family=Gelasio:wght@400;700&display=swap">
<style>
  :root {
    --backdrop: #1f1f1f;
    --leaf-green: #527f3a;
    --flourish-olive: #9aa844;
    --mustard: #fde162;
    --olive-ink: #5f8a3a;
    --ornament-olive: #a9ac42;
    --gold-text: #d8d25a;
  }
  * { margin: 0; padding: 0; box-sizing: border-box; }
  html, body {
    width: 1200px;
    height: 1000px;
    overflow: hidden;
    background: var(--backdrop);
    font-family: "Gelasio", Georgia, serif;
  }
  .canvas { position: relative; width: 1200px; height: 1000px; }

  .card {
    position: absolute;
    width: 630px;
    height: 365px;
    border-radius: 18px;
    overflow: hidden;
  }

  /* Front */
  .card-front {
    left: 300px;
    top: 150px;
    background: var(--leaf-green);
  }
  .flourish-side {
    position: absolute;
    right: 0;
    top: 0;
    width: 210px;
    height: 365px;
    border-radius: 120px 0 0 0;
    background: linear-gradient(to left, rgba(154,168,68,0.75), rgba(154,168,68,0.35));
  }
  .flourish-base {
    position: absolute;
    left: 0;
    bottom: 0;
    width: 630px;
    height: 110px;
    border-radius: 0 140px 0 0;
    background: linear-gradient(to top, rgba(154,168,68,0.7), rgba(154,168,68,0.3));
  }
  .brand-name {
    position: absolute;
    left: 0;
    right: 40px;
    top: 148px;
    text-align: center;
    color: var(--gold-text);
    font-size: 44px;
    font-weight: 400;
    white-space: nowrap;
  }

  /* Back */
  .card-back {
    left: 215px;
    top: 585px;
    background: var(--mustard);
    color: var(--olive-ink);
    text-align: center;
  }
  .corner-ornament {
    position: absolute;
    width: 150px;
    height: 145px;
    background: linear-gradient(135deg, rgba(169,172,66,0.9), rgba(169,172,66,0.55));
  }
  .corner-ornament.top-left { left: 25px; top: 20px; border-radius: 90px 20px 90px 20px; }
  .corner-ornament.top-right { right: 25px; top: 20px; border-radius: 20px 90px 20px 90px; }
  .corner-ornament.bottom-left { left: 25px; bottom: 25px; border-radius: 20px 90px 20px 90px; }
  .corner-ornament.bottom-right { right: 25px; bottom: 25px; border-radius: 90px 20px 90px 20px; }

  .holder-name {
    position: absolute;
    left: 0; right: 0;
    top: 84px;
    font-size: 20px;
    font-weight: 700;
  }
  .holder-role {
    position: absolute;
    left: 0; right: 0;
    top: 108px;
    font-size: 16px;
    font-weight: 400;
  }
  .contact-list {
    position: absolute;
    left: 180px; right: 180px;
    top: 190px;
    list-style: none;
    font-size: 15px;
    white-space: nowrap;
  }
  .contact-list li { height: 35px; }
</style>
</head>
<body>
<main class="canvas">
  <section class="card card-front" aria-label="Card front">
    <div class="flourish-base" role="img" aria-label="Flowing floral swirl ornament along the bottom edge"></div>
    <div class="flourish-side" role="img" aria-label="Flowing floral swirl and leaf ornament on the right side"></div>
    <h1 class="brand-name">Verona by Kettle</h1>
  </section>

  <section class="card card-back" aria-label="Card back">
    <div class="corner-ornament top-left" role="img" aria-label="Baroque acanthus leaf ornament"></div>
    <div class="corner-ornament top-right" role="img" aria-label="Baroque acanthus leaf ornament"></div>
    <div class="corner-ornament bottom-left" role="img" aria-label="Baroque acanthus leaf ornament"></div>
    <div class="corner-ornament bottom-right" role="img" aria-label="Baroque acanthus leaf ornament"></div>

    <h2 class="holder-name">Miriam Kettle</h2>
    <p class="holder-role">Fashion Designer</p>
    <ul class="contact-list">
      <li>04 0261 5847</li>
      <li>veronabykettle@mailbrook.example</li>
      <li>www.socialpage.example/VEronaByKettle</li>
    </ul>
  </section>
</main>
</body>
</html>
```